Harbor Bath & Steam Digital Billboard

This is a digital billboard so we are looking for a fresh design that will capture people's attention. The current billboard is a simple black text "#GottaSteam" over a white background with a picture of an vexaphone with one of our photos (Reference attached) We enjoy how clean and simple this design is, but open to other concepts. Since the weather is getting colder, a lot of people come to our spa because we offer various dry saunas and hot baths in addition to our spa services. We have a few photos for reference on our website information view www.harborbathsteam.example , but you can email me for additional photo content - otto@harborbathsteam.example

Target Market(s)

New Jersey Locals

Colors
0255a3
ec1f27
f37122
ffc214

Requirements
Must have
• Font is "Barlow"
Nice to have
• #GottaSteam hashtag

```html
<!DOCTYPE html>
<html lang="en">
<head>
<meta charset="utf-8">
<title>Harbor Bath &amp; Steam – Digital Billboard</title>
<link href="https://fonts.googleapis.com/css2?family=Montserrat+Alternates:wght@300;500;700&display=swap" rel="stylesheet">
<style>
  :root {
    --stage: #3a3a3a;
    --panel: #fdfdfd;
    --ink: #0c0c0c;
    --teal: #72cdd6;
    --teal-soft: rgba(114, 205, 214, 0);
    --sun-yellow: #fdc85a;
    --sun-orange: #f59a1c;
    --wind-blue: #6fb3e3;
    --wind-light: #cfe8f8;
  }
  * { margin: 0; padding: 0; box-sizing: border-box; }
  html, body {
    width: 1200px;
    height: 880px;
    overflow: hidden;
    background: var(--stage);
  }
  .billboard {
    position: absolute;
    left: 40px;
    top: 276px;
    width: 1120px;
    height: 327px;
    background: var(--panel);
    font-family: "Montserrat Alternates", sans-serif;
    color: var(--ink);
  }
  .weather-icon {
    position: absolute;
    border-radius: 50%;
  }
  .weather-icon--wind {
    left: 60px; top: 51px; width: 88px; height: 65px;
    background: radial-gradient(circle at 45% 50%, var(--wind-blue), var(--wind-light) 75%, transparent 76%);
  }
  .weather-icon--sun {
    left: 58px; top: 203px; width: 88px; height: 88px;
    background: radial-gradient(circle, var(--sun-yellow) 40%, var(--sun-orange) 62%, transparent 64%);
  }
  .temp-line {
    position: absolute;
    font-size: 50px;
    font-weight: 300;
    line-height: 1;
    white-space: nowrap;
  }
  .temp-line strong { font-weight: 700; }
  .temp-line--outside { left: 177px; top: 58px; }
  .temp-line--sauna { left: 189px; top: 232px; }
  .divider-wave {
    position: absolute;
    left: 262px; top: 138px;
    width: 277px; height: 64px;
    border-radius: 50%;
    background: radial-gradient(ellipse at center, var(--teal) 0%, var(--teal) 30%, var(--teal-soft) 72%);
  }
  .brand {
    position: absolute;
    left: 660px; top: 50px;
    width: 400px;
    text-align: center;
    color: var(--ink);
    font-weight: 500;
  }
  .brand__dot {
    width: 84px; height: 84px;
    margin: 0 auto 26px;
    border-radius: 50%;
    background: var(--teal);
  }
  .brand__name {
    font-size: 46px;
    line-height: 1.05;
    letter-spacing: 1px;
  }
  .brand__tag {
    display: block;
    font-size: 24px;
    letter-spacing: 5px;
    margin-top: 6px;
  }
</style>
</head>
<body>
  <main class="billboard">
    <div class="weather-icon weather-icon--wind" role="img" aria-label="Blue wind and snowflake weather icon"></div>
    <p class="temp-line temp-line--outside">Outside Temp <strong>57°</strong></p>

    <div class="divider-wave" role="img" aria-label="Decorative teal wave swoosh"></div>

    <div class="weather-icon weather-icon--sun" role="img" aria-label="Bright orange sun weather icon"></div>
    <p class="temp-line temp-line--sauna">Sauna Temp <strong>92°</strong></p>

    <div class="brand">
      <div class="brand__dot"></div>
      <p class="brand__name">Harbor Bath<span class="brand__tag">&amp; STEAM</span></p>
    </div>
  </main>
</body>
</html>
```